Automotive component supplier needs a business card design

We need a business card design for our company called Velran Global Components Ltd based in the UK. We are a supplier of interior and exterior components to premium car manufacturers such as Corvel Ashby, Hadley Fenn, Marquist and Tavarelli. We would like to see a modern business card design that uses the colour blue.

Target Market(s)

Premium automotive car manufacturers.

Industry/Entity Type

Automotive

Contact Information for Business Card

Company Name : Velran Global Components Limited
Address: 17 Marlow Yard, Upper Heath, Warwick, CV31 8QL, United Kingdom
Web Address : www.velrancomponents-example.co.uk

Font styles to use
Other font styles liked:
• Helvetica

Colors
3176b5
0255a3
85acd3
cfdeed
cee9f5
85cae6
34a6d7
0692cd
9bcb3c

Requirements
Must have
• Clear company logo and a mixture of blue colours.
Nice to have
• A high quality modern image.
Should not have
• Multiple colours.

```html
<!DOCTYPE html>
<html lang="en">
<head>
<meta charset="utf-8">
<title>Velran Global Components – Business Card</title>
<link href="https://fonts.googleapis.com/css2?family=Lato:wght@400;700&display=swap" rel="stylesheet">
<style>
  :root {
    --brand-blue: #0692cd;
    --brand-blue-deep: #0a86c0;
    --accent-green: #9bcb3c;
    --card-white: #ffffff;
    --ink: #1a1a1a;
    --page-bg: #eeeeee;
  }
  * { margin: 0; padding: 0; box-sizing: border-box; }
  html, body {
    width: 1200px; height: 586px; overflow: hidden;
    background: var(--page-bg);
    font-family: "Lato", Helvetica, Arial, sans-serif;
  }
  .stage { position: relative; width: 1200px; height: 586px; }

  .card {
    position: absolute; top: 129px;
    width: 502px; height: 301px;
  }

  /* Front */
  .card-front { left: 61px; background: var(--brand-blue); color: var(--card-white); }
  .front-wordmark {
    position: absolute; left: 0; right: 0; top: 110px;
    text-align: center;
    font-weight: 700; font-size: 38px; letter-spacing: 1px;
    color: var(--card-white);
  }
  .front-web {
    position: absolute; left: 0; right: 0; top: 264px;
    text-align: center;
    font-size: 10.5px; font-weight: 700; letter-spacing: 2px;
  }

  /* Back */
  .card-back { left: 619px; background: var(--card-white); }
  .identity {
    position: absolute; right: 289px; top: 113px; text-align: right;
  }
  .person-name { color: var(--brand-blue); font-weight: 700; font-size: 14px; line-height: 18px; }
  .person-role { color: var(--ink); font-size: 11px; line-height: 14px; margin-top: 4px; }
  .address {
    color: var(--brand-blue); font-weight: 700; font-size: 11px; line-height: 15px;
    margin-top: 19px;
  }
  .divider {
    position: absolute; left: 241px; top: 88px; width: 2px; height: 128px;
    background: linear-gradient(to bottom, rgba(155,203,60,0), var(--accent-green) 35%, var(--accent-green) 65%, rgba(155,203,60,0));
  }
  .contacts { position: absolute; left: 267px; top: 123px; list-style: none; }
  .contacts li {
    display: flex; align-items: center; height: 24.5px;
    font-size: 12px; color: var(--ink);
  }
  .contacts svg { width: 14px; height: 14px; margin-right: 8px; flex: none; }
  .partner-band {
    position: absolute; left: 0; right: 0; bottom: 0; height: 25px;
    background: var(--brand-blue-deep);
    display: flex; align-items: center; justify-content: center;
    color: var(--card-white); font-size: 11.5px; font-weight: 700;
  }
  .partner-band .sep { color: #0b2740; margin: 0 4px; font-weight: 400; }
</style>
</head>
<body>
<div class="stage">
  <section class="card card-front">
    <div class="front-wordmark">Velran Global Components</div>
    <div class="front-web">www.velrancomponents-example.co.uk</div>
  </section>

  <section class="card card-back">
    <div class="identity">
      <div class="person-name">Maren Solway</div>
      <div class="person-role">Director</div>
      <div class="address">17 Marlow Yard, Upper Heath<br>Warwick, CV31 8QL, UK</div>
    </div>
    <div class="divider"></div>
    <ul class="contacts">
      <li>
        <svg viewBox="0 0 14 14" aria-hidden="true"><rect x="3.5" y="0.8" width="7" height="12.4" rx="1.2" fill="none" stroke="#0692cd" stroke-width="1.3"/><line x1="5.5" y1="11" x2="8.5" y2="11" stroke="#0692cd" stroke-width="1"/></svg>
        (234) 555 0194
      </li>
      <li>
        <svg viewBox="0 0 14 14" aria-hidden="true"><path d="M1 5 Q7 1 13 5 L12 7 L9.5 6 L9.5 4.8 Q7 4 4.5 4.8 L4.5 6 L2 7 Z" fill="#0692cd"/><path d="M3.5 8 L5 6.5 L9 6.5 L10.5 8 L11 12.5 L3 12.5 Z" fill="#0692cd"/><circle cx="7" cy="9.6" r="1.3" fill="#fff"/></svg>
        0421 555 0386
      </li>
      <li>
        <svg viewBox="0 0 14 14" aria-hidden="true"><rect x="1" y="3" width="12" height="8.5" fill="#0692cd"/><path d="M1 3 L7 8 L13 3" fill="none" stroke="#fff" stroke-width="1"/></svg>
        msolway@velran-example.co.uk
      </li>
    </ul>
    <div class="partner-band">
      Corvel Ashby<span class="sep">|</span>Hadley Fenn<span class="sep">|</span>Marquist<span class="sep">|</span>Tavarelli
    </div>
  </section>
</div>
</body>
</html>
```